Corvane Capital Business Cards

These are professional business cards that are for my family office.
Put fake emails and phone numbers as of now until I finalize those components. This family office controls my families investments, assets, and future. The cards should be professional.
..
.
.
.
I just uploaded another variation of a logo I would like to see as a business card to I am inbeteen which logo to use

Target Market(s)

business

Industry/Entity Type

business

Contact Information for Business Card

Professional, wealth related, finance related.

Requirements
Must have
• Logo

```html
<!DOCTYPE html>
<html lang="en">
<head>
<meta charset="utf-8">
<title>Corvane Capital Business Cards</title>
<link href="https://fonts.googleapis.com/css2?family=Cinzel:wght@600&family=Poppins:wght@400;500;700&display=swap" rel="stylesheet">
<style>
  :root {
    --backdrop: #e3e6e8;
    --navy: #171c2a;
    --white: #ffffff;
    --dot-grey: #a6a6a6;
  }
  * { margin: 0; padding: 0; box-sizing: border-box; }
  html, body { width: 1200px; height: 960px; overflow: hidden; }
  body { background: var(--backdrop); position: relative; font-family: "Poppins", sans-serif; }

  .card { position: absolute; left: 250px; width: 701px; height: 400px; overflow: hidden; }

  /* Front */
  .card-front { top: 60px; background: var(--navy); }
  .front-mark {
    position: absolute; left: 337px; top: 158px;
    width: 28px; height: 28px; border-radius: 50%; background: var(--dot-grey);
  }
  .front-name {
    position: absolute; left: 0; width: 100%; top: 278px; text-align: center;
    font-family: "Cinzel", serif; font-weight: 600; font-size: 40px; line-height: 1;
    color: var(--white);
  }

  /* Back */
  .card-back { top: 500px; background: var(--white); }
  .back-lower { position: absolute; left: 0; top: 200px; width: 100%; height: 200px; background: var(--navy); }
  .back-brand {
    position: absolute; left: 24px; top: 36px;
    font-family: "Cinzel", serif; font-weight: 600; font-size: 38px; line-height: 1;
    color: var(--navy);
  }
  .accent-bar { position: absolute; left: 0; top: 126px; width: 19px; height: 53px; background: var(--navy); }
  .person-name {
    position: absolute; left: 27px; top: 122px;
    font-size: 35px; line-height: 1; color: var(--navy); font-weight: 400;
  }
  .person-name strong { font-weight: 700; }
  .person-role {
    position: absolute; left: 28px; top: 164px;
    font-size: 17px; font-weight: 500; line-height: 1; color: var(--navy);
  }
  .address {
    position: absolute; left: 27px; top: 226px;
    font-size: 18.5px; line-height: 26px; color: var(--white); letter-spacing: 0.3px;
  }
  .contact-list { position: absolute; left: 26px; top: 302px; list-style: none; }
  .contact-list li {
    display: flex; align-items: center; gap: 11px; height: 26px;
    font-size: 18.5px; color: var(--white); letter-spacing: 0.3px;
  }
  .contact-list svg { width: 17px; height: 17px; flex: none; }
  .back-disc {
    position: absolute; left: 388px; top: 62px;
    width: 280px; height: 280px; border-radius: 50%; background: var(--white);
  }
</style>
</head>
<body>

  <section class="card card-front" aria-label="Card front">
    <div class="front-mark"></div>
    <div class="front-name">Corvane Capital</div>
  </section>

  <section class="card card-back" aria-label="Card back">
    <div class="back-lower"></div>
    <div class="back-brand">Corvane Capital</div>
    <div class="accent-bar"></div>
    <div class="person-name"><strong>Mira</strong> Halden</div>
    <div class="person-role">Founder &amp; CEO</div>

    <address class="address" style="font-style:normal">
      1480 Elmridge Ave. Suite 300<br>
      Arlington, TX 76010
    </address>

    <ul class="contact-list">
      <li>
        <svg viewBox="0 0 24 24" aria-hidden="true"><path fill="#fff" d="M6.6 10.8a15.1 15.1 0 0 0 6.6 6.6l2.2-2.2c.3-.3.7-.4 1-.2 1.1.4 2.3.6 3.6.6.6 0 1 .4 1 1V20c0 .6-.4 1-1 1C10.6 21 3 13.4 3 4c0-.6.4-1 1-1h3.5c.6 0 1 .4 1 1 0 1.3.2 2.5.6 3.6.1.3 0 .7-.2 1z"/></svg>
        (555) 214-0387
      </li>
      <li>
        <svg viewBox="0 0 24 24" aria-hidden="true"><circle cx="12" cy="12" r="9" fill="none" stroke="#fff" stroke-width="2"/><path d="M3 12h18M12 3c3 3 3 15 0 18M12 3c-3 3-3 15 0 18" fill="none" stroke="#fff" stroke-width="1.6"/></svg>
        info@yourwebsite.com
      </li>
      <li>
        <svg viewBox="0 0 24 24" aria-hidden="true"><rect x="2" y="5" width="20" height="15" rx="1.5" fill="#fff"/><path d="M2.5 6l9.5 7 9.5-7" fill="none" stroke="#171c2a" stroke-width="1.8"/></svg>
        www.yourwebsite.com
      </li>
    </ul>

    <div class="back-disc"></div>
  </section>

</body>
</html>
```